Road Construction Company needs business cards

We would like a new business card designed for our business.

We're a road construction company based in Qld, Australia.

Can the business card please have the following information on it.

Name: Warren Halbeck
Position: General Manager
Phone: 0472 915 348
Email: Warren.halbeck@tovrin.com.au
Address: 87 Marrow Ave, Pendlebay, QLD, 4023
Website: www.tovrin.com.au

Visually we'd like the card to be professional and simple.

Attached is our logo.

Our website is www.tovrin.com.au

Target Market(s)

Men aged 25-60

Contact Information for Business Card

As listed in project description

Font styles to use
Serif

Requirements
Must have
• Large logo on back of card

```html
<!DOCTYPE html>
<html lang="en">
<head>
<meta charset="utf-8">
<title>Tovrin Business Card</title>
<link rel="stylesheet" href="https://fonts.googleapis.com/css2?family=Exo+2:wght@400;700;800&display=swap">
<style>
  :root {
    --backdrop: #2b2b2d;
    --card-white: #ffffff;
    --brand-blue: #0a4fa3;
    --accent-blue: #2e8fd6;
    --back-blue: #0654a9;
    --back-blue-deep: #044690;
    --ink: #1b1b1b;
    --rule: #9a9a9a;
  }
  * { box-sizing: border-box; margin: 0; padding: 0; }
  html, body {
    width: 1200px; height: 1108px; overflow: hidden;
    background: var(--backdrop);
    font-family: "Exo 2", sans-serif;
  }
  .stage {
    position: relative; width: 1200px; height: 1108px;
    display: flex; align-items: center; justify-content: center; gap: 90px;
  }
  .card {
    width: 400px; height: 655px; border-radius: 26px; overflow: hidden;
    position: relative;
  }
  .card-front {
    background: var(--card-white);
    display: flex; flex-direction: column; align-items: center;
    text-align: center; color: var(--ink);
  }
  .brand-name {
    margin-top: 150px;
    font-size: 62px; font-weight: 800; letter-spacing: 4px;
    color: var(--brand-blue); line-height: 1;
  }
  .person { margin-top: 140px; }
  .person-name {
    font-size: 27px; font-weight: 800; letter-spacing: 2px;
    text-transform: uppercase; color: var(--brand-blue); line-height: 1.1;
  }
  .person-role {
    font-size: 21px; font-weight: 400; color: var(--accent-blue); margin-top: 2px;
  }
  .icon-rule {
    display: flex; align-items: center; gap: 10px; width: 300px; margin-top: 12px;
  }
  .icon-rule::before, .icon-rule::after {
    content: ""; flex: 1; height: 1px; background: var(--rule);
  }
  .icon-set { display: flex; gap: 5px; }
  .icon-set svg { width: 30px; height: 30px; display: block; }
  .contact-list {
    list-style: none; margin-top: 10px;
    font-size: 19px; line-height: 1.35;
  }
  .web-domain { color: var(--brand-blue); }
  .rule { width: 300px; height: 1px; background: var(--rule); margin: 14px 0 12px; }
  .address { font-style: normal; font-size: 19px; line-height: 1.35; }

  .card-back { background: var(--back-blue); }
  .back-pattern {
    position: absolute; inset: 0;
    background: linear-gradient(160deg, var(--back-blue) 0%, var(--back-blue-deep) 55%, var(--back-blue) 100%);
  }
  .back-brand {
    position: absolute; left: 0; right: 0; bottom: 150px;
    text-align: center;
    font-size: 58px; font-weight: 800; letter-spacing: 4px;
    color: var(--card-white); line-height: 1;
  }
</style>
</head>
<body>
<main class="stage">
  <section class="card card-front" aria-label="Card front">
    <div class="brand-name">TOVRIN</div>

    <div class="person">
      <h1 class="person-name">Warren Halbeck</h1>
      <p class="person-role">General Manager</p>
    </div>

    <div class="icon-rule">
      <div class="icon-set">
        <svg viewBox="0 0 30 30" aria-label="Phone">
          <rect width="30" height="30" rx="5" fill="#0a4fa3"/>
          <path d="M10 8c1-1 2 0 3 2s1 2 0 3c1 2 2 3 4 4 1-1 2-1 3 0s3 2 2 3c-1 2-3 2-5 1-4-2-7-5-8-9-1-2 0-3 1-4z" fill="#fff"/>
        </svg>
        <svg viewBox="0 0 30 30" aria-label="Email">
          <rect width="30" height="30" rx="5" fill="#0a4fa3"/>
          <rect x="7" y="9" width="16" height="12" fill="none" stroke="#fff" stroke-width="1.8"/>
          <path d="M7 9l8 7 8-7" fill="none" stroke="#fff" stroke-width="1.8"/>
        </svg>
        <svg viewBox="0 0 30 30" aria-label="Website">
          <rect width="30" height="30" rx="5" fill="#0a4fa3"/>
          <circle cx="15" cy="15" r="8" fill="none" stroke="#fff" stroke-width="1.8"/>
          <ellipse cx="15" cy="15" rx="3.5" ry="8" fill="none" stroke="#fff" stroke-width="1.4"/>
          <path d="M7 15h16" stroke="#fff" stroke-width="1.4"/>
        </svg>
      </div>
    </div>

    <ul class="contact-list">
      <li>0472 915 348</li>
      <li>Warren.halbeck@tovrin.com.au</li>
      <li>www.<span class="web-domain">tovrin</span>.com.au</li>
    </ul>

    <div class="rule"></div>

    <address class="address">
      87 Marrow Ave<br>
      Pendlebay, QLD, 4023
    </address>
  </section>

  <section class="card card-back" aria-label="Card back">
    <div class="back-pattern" role="img" aria-label="Repeating tonal brand pattern in deep blue"></div>
    <div class="back-brand">TOVRIN</div>
  </section>
</main>
</body>
</html>
```